Civora88 - a Political Plebescite app.

There is a current app in the App Store (worldwide) and Play Store (worldwide) called yourStance (with an owl logo). The UX needs to be redesigned to make it more visually pleasing.

The requirement is to build a UX that is suitable for both iOS and Android - i.e. consistent look for both platforms. The design is to span the variety of sizes available from smart devices - phones and tablets. The layout as it stands is portrait only, and a secondary design to encompass landscape is wanted.

You would need to download the app to get a feel for all the functionality - there are 3 visible forms (currently) and a hidden form, that will be used in the near future - this hidden form will look similar to the main (first) form.

To get full functionality you need to do the following:
Go to the Options page
Toggle the top slide
Click on UNREGISTERED
Select a state/territory

I know this is a bit non-intuitive - in the "real" product these steps are automated - but for this release the user gets to choose.

Once this is done - the other button(s) appear in the top left of the screen - and data is available to be displayed.

The current forms are included in this brief. The Options screen will ultimately not be showing all the current data, only the lower slider (or other indicator) and the associated version and copyright notices. The hidden screen is much like the main screen - showing the name of the bill and information pertaining to that bill - there needs to be a button (or action site) to toggle between the main and this hidden screen.

Target Market(s)

All eligable voters (currently in Australia)

Industry/Entity Type

Political

Requirements
Should not have
• Do not present to me my own/existing design with the only change being colours and label layout.

```html
<!DOCTYPE html>
<html lang="en">
<head>
<meta charset="utf-8">
<title>Civora88 – Bill Vote</title>
<link rel="stylesheet" href="https://fonts.googleapis.com/css2?family=Inter:wght@300;400;600;700&display=swap">
<style>
  :root {
    --bg: #ffffff;
    --bar-bg: #ececec;
    --bar-line: #c8c8c8;
    --ink: #1c1c1c;
    --ink-soft: #444444;
    --link: #1a8cff;
    --card-head: #0a7cff;
    --card-foot: #eeeeee;
    --online: #2ecc71;
    --yes: #2ecc71;
    --abstain: #f4d56f;
    --no: #ec644b;
    --icon: #222222;
  }
  * { box-sizing: border-box; margin: 0; padding: 0; }
  html, body { width: 676px; height: 1200px; overflow: hidden; background: var(--bg); }
  body { font-family: "Inter", "Helvetica Neue", Arial, sans-serif; color: var(--ink); position: relative; }

  .top-bar { position: absolute; left: 0; top: 0; width: 676px; height: 135px; background: var(--bar-bg); border-bottom: 1px solid var(--bar-line); }
  .status-bar { position: absolute; left: 0; top: 0; width: 100%; height: 40px; }
  .status-time { position: absolute; left: 0; right: 0; top: 9px; text-align: center; font-size: 20px; font-weight: 600; }
  .status-signal { position: absolute; left: 16px; top: 13px; }
  .status-battery { position: absolute; right: 12px; top: 9px; display: flex; align-items: center; gap: 4px; font-size: 20px; font-weight: 400; }

  .nav-link { position: absolute; top: 86px; font-size: 23px; font-weight: 400; color: var(--link); }
  .nav-help { left: 25px; }
  .nav-settings { right: 19px; }
  .assembly { position: absolute; left: 0; right: 0; top: 65px; text-align: center; }
  .assembly-label { font-size: 13px; font-weight: 600; letter-spacing: .2px; }
  .assembly-name { display: inline-flex; align-items: center; gap: 12px; margin-top: 3px; font-size: 28px; font-weight: 300; }

  .progress { position: absolute; left: 0; right: 0; top: 166px; text-align: center; font-size: 23px; font-weight: 700; }
  .status-pill { position: absolute; left: 489px; top: 169px; width: 141px; height: 34px; border: 1.5px solid #555; border-radius: 17px; display: flex; align-items: center; justify-content: center; gap: 10px; font-size: 19px; font-weight: 700; }
  .status-pill .dot { width: 13px; height: 13px; border-radius: 50%; background: var(--online); }

  .card-stack-layer { position: absolute; height: 40px; background: #efefef; border-radius: 12px; box-shadow: 0 1px 3px rgba(0,0,0,.35); }
  .layer-3 { left: 60px; width: 562px; top: 910px; }
  .layer-2 { left: 52px; width: 574px; top: 897px; }
  .bill-card { position: absolute; left: 43px; top: 255px; width: 590px; height: 664px; background: #fff; border-radius: 14px; overflow: hidden; box-shadow: 0 1px 4px rgba(0,0,0,.4); }
  .bill-head { height: 152px; background: var(--card-head); color: #fff; padding: 26px 38px 0; }
  .bill-title { font-size: 24px; font-weight: 700; line-height: 1.15; }
  .bill-subtitle { font-size: 16px; font-weight: 400; line-height: 22px; margin-top: 2px; }
  .bill-year { font-size: 16px; font-weight: 700; margin-top: 14px; }
  .bill-summary { padding: 32px 38px 0; font-size: 27px; font-weight: 300; line-height: 33.4px; }
  .bill-action { position: absolute; left: 0; bottom: 0; width: 100%; height: 84px; background: var(--card-foot); display: flex; align-items: center; justify-content: center; font-size: 27px; font-weight: 700; color: var(--ink-soft); letter-spacing: .3px; }

  .vote-button { position: absolute; border-radius: 50%; background: #fff; box-shadow: 0 1px 4px rgba(0,0,0,.35); display: flex; align-items: center; justify-content: center; }
  .vote-button .face { border-radius: 50%; display: flex; align-items: center; justify-content: center; }
  .vote-yes { left: 121px; top: 1003px; width: 144px; height: 144px; }
  .vote-yes .face { width: 120px; height: 120px; background: var(--yes); }
  .vote-abstain { left: 286px; top: 1023px; width: 104px; height: 104px; }
  .vote-abstain .face { width: 86px; height: 86px; background: var(--abstain); }
  .vote-no { left: 415px; top: 1003px; width: 144px; height: 144px; }
  .vote-no .face { width: 120px; height: 120px; background: var(--no); }
  .abstain-bar { width: 60px; height: 17px; border-radius: 9px; background: var(--ink-soft); }
</style>
</head>
<body>
  <header class="top-bar">
    <div class="status-bar">
      <svg class="status-signal" width="100" height="18" viewBox="0 0 100 18" aria-hidden="true">
        <g fill="#222"><circle cx="6" cy="8" r="5.5"/><circle cx="19" cy="8" r="5.5"/><circle cx="32" cy="8" r="5.5"/><circle cx="45" cy="8" r="5.5"/><circle cx="58" cy="8" r="5.5"/></g>
        <g fill="none" stroke="#222" stroke-width="2.6" stroke-linecap="round"><path d="M70 5 a14 14 0 0 1 18 0"/><path d="M73.5 9 a8.5 8.5 0 0 1 11 0"/></g>
        <circle cx="79" cy="13" r="2.2" fill="#222"/>
      </svg>
      <div class="status-time">9:41 AM</div>
      <div class="status-battery">100%
        <svg width="42" height="20" viewBox="0 0 42 20" aria-hidden="true"><rect x="1" y="1" width="36" height="18" rx="3" fill="none" stroke="#222" stroke-width="1.6"/><rect x="3.5" y="3.5" width="31" height="13" rx="1.5" fill="#222"/><rect x="38.5" y="6.5" width="2.5" height="7" rx="1" fill="#222"/></svg>
      </div>
    </div>
    <span class="nav-link nav-help">Help</span>
    <div class="assembly">
      <div class="assembly-label">LEGISLATIVE ASSEMBLY</div>
      <div class="assembly-name">
        <svg width="14" height="8" viewBox="0 0 14 8" aria-hidden="true"><path d="M0 0 H14 L7 8 Z" fill="#222"/></svg>
        Northern Territory
      </div>
    </div>
    <span class="nav-link nav-settings">Settings</span>
  </header>

  <div class="progress">4/10</div>
  <div class="status-pill"><span class="dot"></span>ONLINE</div>

  <div class="card-stack-layer layer-3"></div>
  <div class="card-stack-layer layer-2"></div>
  <article class="bill-card">
    <div class="bill-head">
      <h1 class="bill-title">Monitoring of Places of Detention</h1>
      <p class="bill-subtitle">(Optional Protocol to the Convention Against Torture)<br>&nbsp;- National Uniform Legislation</p>
      <p class="bill-year">Bill 2013</p>
    </div>
    <p class="bill-summary">An act to enable the Optional Protocol to the Convention against Torture and other Cruel, Inhuman or Degrading Treatment or Punishment to be given effect within the Territory.</p>
    <div class="bill-action">VIEW BILL</div>
  </article>

  <div class="vote-button vote-yes" aria-label="Vote yes"><div class="face">
    <svg width="54" height="50" viewBox="0 0 54 50" aria-hidden="true"><g fill="var(--icon)"><rect x="38" y="20" width="12" height="28" rx="2"/><path d="M4 22 Q4 19 7 19 H17 L22 4 Q24 0 28 2 Q31 4 30 9 L28 19 H31 Q35 19 35 23 V44 Q35 48 31 48 H8 Q4 48 4 44 Z"/></g></svg>
  </div></div>
  <div class="vote-button vote-abstain" aria-label="Abstain"><div class="face"><div class="abstain-bar"></div></div></div>
  <div class="vote-button vote-no" aria-label="Vote no"><div class="face">
    <svg width="54" height="50" viewBox="0 0 54 50" aria-hidden="true"><g fill="var(--icon)" transform="rotate(180 27 25)"><rect x="38" y="20" width="12" height="28" rx="2" transform="translate(-34 0)"/><path d="M19 22 Q19 19 22 19 H32 L37 4 Q39 0 43 2 Q46 4 45 9 L43 19 H46 Q50 19 50 23 V44 Q50 48 46 48 H23 Q19 48 19 44 Z"/></g></svg>
  </div></div>
</body>
</html>
```